Brisk. Technology Logistics Software platform.

A modern looking and feeling website for a logistics software platform.
We connect retailers or wholesale parcel distributors to worldwide delivery solutions.
Methods tend to be road and air transport to final mile courier companies and post offices all over the world.
Our platform is for ecommerce distribution. A customer uses BRISK to enable them to connect to worldwide companies who will track and trace the delivery of their goods.

Target Market(s)

Onllne retailers. Markert Places such as Vendora and Tradelo. Wholesale third party logistics and packaging companies. Delivery companies based in the UK looking to expand overseas.

Number of Pages Required

5+ page

Font styles to use
Sans Serif

Colors
aaaaaa
dbdbdb
e6e6e6
c4c4c4
cbcbcb
c9c9c9
ec1f27
3176b5
0355a3

Requirements
Must have
• Landing Page.
• What we do.
• Who we are.
• Modules.
• Testimonies (password protected)
• Contact us.
• Interactive for mobile operating systems.
• Scrolling website.
• Short stock video showing on key pages.
• Very well polished fonts and buttons. A sharp and well executed website is required.
• Simplicity in feeling.
• To the point on message.
• Refined wording and copyrighting / messaging
• A link to our sub brand and product Brisk Parcels
• Capture interest so people read further.
Nice to have
• A polished video to explain what we do on landing page. Clipmarrow.net have some good options but not sure how professional they will look.
Should not have
• Bad graphics and colours.
• Not lots of clicks. Less as possible
• Complex message

```html
<!DOCTYPE html>
<html lang="en">
<head>
<meta charset="utf-8">
<title>Brisk. Technology – Website Screens</title>
<link rel="stylesheet" href="https://fonts.googleapis.com/css2?family=Orbitron:wght@700;800&family=Open+Sans:wght@400;600;700&display=swap">
<style>
  :root {
    --red: #e4001f;
    --red-bright: #ec1f27;
    --navy: #0355a3;
    --blue: #3176b5;
    --grey: #aaaaaa;
    --grey-dark: #8a8a8a;
    --board: #eff4f9;
    --ink: #1d1d1d;
    --white: #ffffff;
  }
  * { box-sizing: border-box; margin: 0; padding: 0; }
  html, body { width: 1200px; height: 708px; overflow: hidden; }
  body { background: var(--board); font-family: "Open Sans", Arial, sans-serif; position: relative; }

  .screen { position: absolute; top: 35px; width: 541px; box-shadow: 0 2px 6px rgba(0,0,0,.18); overflow: hidden; background: var(--white); }

  /* Landing screen */
  .landing { left: 43px; height: 328px; }
  .landing .hero-photo { position: absolute; inset: 0 0 22px 0;
    background: radial-gradient(ellipse at 50% 40%, #4b4a44 0%, #2d2c29 55%, #1a1a19 100%); }
  .landing .brand { position: absolute; top: 38px; left: 0; width: 100%; text-align: center; }
  .brand-mark { display: inline-flex; align-items: center; gap: 6px; font-weight: 700; color: var(--red-bright); }
  .brand-mark .dot { border-radius: 50%; background: var(--red-bright); display: inline-block; }
  .landing .brand-mark { font-size: 40px; }
  .landing .brand-mark .dot { width: 34px; height: 34px; }
  .landing h1 { position: absolute; top: 132px; width: 100%; text-align: center; font-family: "Orbitron", "Open Sans", sans-serif; font-weight: 800; font-size: 20px; color: var(--white); letter-spacing: .5px; }
  .landing .intro { position: absolute; top: 170px; left: 85px; width: 371px; text-align: center; color: var(--white); font-size: 6.6px; font-weight: 600; line-height: 16.3px; }
  .play { position: absolute; width: 34px; height: 34px; }
  .landing .play { left: 253px; top: 238px; }
  .landing .legal { position: absolute; bottom: 0; left: 0; width: 100%; height: 22px; background: var(--red); color: var(--white); font-size: 6px; display: flex; align-items: center; justify-content: center; }

  /* Home screen */
  .home { left: 615px; height: 638px; border-bottom: 2px solid var(--red-bright); }
  .home .hero-photo { position: absolute; top: 0; left: 0; width: 100%; height: 273px;
    background: linear-gradient(160deg, #1f2c4a 0%, #2f4f86 45%, #3e64a4 100%); }
  .home .header { position: absolute; top: 20px; left: 50px; right: 50px; display: flex; justify-content: space-between; align-items: center; }
  .home .brand-mark { font-size: 26px; }
  .home .brand-mark .dot { width: 22px; height: 22px; }
  .nav { display: flex; gap: 24px; font-size: 7.3px; font-weight: 600; color: var(--white); }
  .nav a { color: inherit; text-decoration: none; padding-bottom: 4px; }
  .nav .active { border-bottom: 1.5px solid var(--red-bright); }
  .home h2 { position: absolute; top: 105px; left: 50px; width: 400px; font-family: "Orbitron", "Open Sans", sans-serif; font-weight: 800; font-size: 15.5px; line-height: 26px; color: var(--white); }
  .home .play { left: 50px; top: 200px; }
  .emblem { position: absolute; left: 244px; top: 245px; width: 54px; height: 54px; border-radius: 50%; background: var(--red-bright); border: 3px solid var(--white); box-shadow: 0 1px 3px rgba(0,0,0,.2); }
  .about { position: absolute; top: 318px; left: 80px; width: 381px; text-align: center; font-size: 7.2px; line-height: 19.1px; color: var(--ink); }
  .about a { color: var(--red-bright); }
  .band { position: absolute; top: 451px; left: 0; width: 100%; height: 82px; background: var(--red); color: var(--white); padding: 23px 53px 0; font-weight: 700; font-size: 9.2px; line-height: 23px; }
  .band::before { content: ""; position: absolute; top: 0; left: 263px; border: 8px solid transparent; border-top-color: var(--white); border-bottom: 0; }
  .pill { display: inline-block; padding: 0 12px; border-radius: 11px; font-size: 6.6px; line-height: 21px; margin: 0 3px; vertical-align: middle; }
  .pill.parcel { background: var(--navy); }
  .pill.tech { background: var(--grey); }
  .site-footer { position: absolute; top: 533px; left: 0; width: 100%; height: 103px; }
  .site-footer .brand-mark { position: absolute; left: 51px; top: 32px; font-size: 26px; }
  .site-footer .brand-mark .dot { width: 22px; height: 22px; }
  .foot-info { position: absolute; right: 51px; top: 26px; text-align: right; font-size: 6.9px; color: #333; line-height: 20px; }
  .foot-info .links { font-weight: 600; }
  .foot-info .copyright { color: #555; font-size: 6.4px; }
  .ico { display: inline-block; width: 5px; height: 5px; background: var(--red-bright); margin: 0 3px 0 8px; border-radius: 1px; }
</style>
</head>
<body>

<section class="screen landing">
  <div class="hero-photo" role="img" aria-label="Aerial view of a distribution warehouse with lorries parked at loading bays, darkened"></div>
  <div class="brand"><span class="brand-mark"><span class="dot"></span>Brisk.</span></div>
  <h1>BRISK.TECHNOLOGY... OUR FOCUS</h1>
  <p class="intro">We provide advanced software solutions to ensure you connect with global ecommerce delivery carriers You can manage your Global Delivery Network in one place, with Our software will enable you monitor the productivity and reporting of your ecommerce deliveries Manage your carriers, your delivery speeds, and your costs</p>
  <svg class="play" viewBox="0 0 34 34"><circle cx="17" cy="17" r="16" fill="none" stroke="#fff" stroke-width="1.2"/><path d="M13 10 L24 17 L13 24 Z" fill="none" stroke="#fff" stroke-width="1.2" stroke-linejoin="round"/></svg>
  <div class="legal">© copyright 2018 Brisk Technology.All Rights Reserved &nbsp;|&nbsp; Privacy policy</div>
</section>

<section class="screen home">
  <div class="hero-photo" role="img" aria-label="Aerial view of lorries at a distribution warehouse with a blue tint"></div>
  <header class="header">
    <span class="brand-mark"><span class="dot"></span>Brisk.</span>
    <nav class="nav">
      <a class="active">HOME</a>
      <a>SOLUTIONS ⌄</a>
      <a>TESTIMONIAL LOGIN ⌄</a>
      <a>CONTACT US</a>
    </nav>
  </header>
  <h2>Brisk. Technology and Parcel Solutions Built To Help Develop &amp; Manage Your Global Delivery Network</h2>
  <svg class="play" viewBox="0 0 34 34"><circle cx="17" cy="17" r="16" fill="none" stroke="#fff" stroke-width="1.2"/><path d="M13 10 L24 17 L13 24 Z" fill="none" stroke="#fff" stroke-width="1.2" stroke-linejoin="round"/></svg>
  <div class="emblem"></div>
  <p class="about">Working closely with Ecommerce, Brisk. Technology have developed solutions purely focused on delivering what’s required within the global delivery marketplace. Meeting all needs and more for Retailers and Global Delivery Solution providers<br>Allowing customers to grow at a fast pace; most importantly providing tools to help them manage their global delivery network supported by “<a>Dynamic Real Time Visibility</a>” management tools</p>
  <div class="band">ENSURING <span class="pill parcel">BRISK PARCEL</span><span class="pill tech">BRISK TECHNOLOGY</span> SOLUTIONS EVOLVE TO SUIT OUR CUSTOMERS<br>BUSINESS REQUIREMENTS</div>
  <footer class="site-footer">
    <span class="brand-mark"><span class="dot"></span>Brisk.</span>
    <div class="foot-info">
      <div class="links">HOME &nbsp;|&nbsp; SOLUTIONS &nbsp;|&nbsp; TESTIMONIAL LOGIN &nbsp;|&nbsp; CONTACT US</div>
      <div><span class="ico"></span>234 Harbour Row, Leeds &nbsp;|<span class="ico"></span>1 800 555 0142 &nbsp;|<span class="ico"></span>hello@brisktech.co</div>
      <div class="copyright">Copyright 2018 Brisk Technology.All Rights Reserved</div>
    </div>
  </footer>
</section>

</body>
</html>
```